Tarn Workforce Tri Fold Brochure

My company is a recruiting/staffing firm. I need a design that is going to be professional, bright, young, hip and fun. Pictures are key! We want people working in an office, packaging, food production and/or light industrial environment. Must embrace DIVERSITY. Please use the 4 primary colors from the Tarn Logo to accent the piece, but not too busy. I am including the content that I would like to be included in the trifold as well as a sample of a trifold I have used in the past in addition to a couple of logos. My website is www.TarnWorkforce-example.com for look and feel.

Target Market(s)

Logistics, Distribution and Manufacturing companies

Industry/Entity Type

Staffing

Requirements
Must have
• Clean, colorful, eye catching, great pictures and graphics. Photo's of diverse people working, in a office, or production setting.
Nice to have
• Must be professional
Should not have
• Not too busy.

```html
<!DOCTYPE html>
<html lang="en">
<head>
<meta charset="utf-8">
<title>Tarn Workforce Tri-Fold Brochure</title>
<link href="https://fonts.googleapis.com/css2?family=Roboto:wght@300;400;500;700&family=Roboto+Condensed:wght@400;700&display=swap" rel="stylesheet">
<style>
:root{
  --red:#e8453c;
  --green:#1f8a3e;
  --yellow:#f5c51b;
  --navy:#3a3d8c;
  --ink:#333;
  --muted:#6d6d6d;
  --paper:#fff;
  --backdrop:#ececec;
}
*{box-sizing:border-box;margin:0;padding:0}
html,body{width:900px;height:1200px;overflow:hidden;background:var(--backdrop)}
body{font-family:"Roboto",Arial,sans-serif;color:var(--ink);position:relative}
.sheet{position:absolute;left:50px;width:800px;height:580px;background:var(--paper);box-shadow:0 4px 14px rgba(0,0,0,.18);overflow:hidden}
.sheet--outside{top:10px}
.sheet--inside{top:610px}
.panel{position:absolute;top:0;height:580px;width:267px}
.panel--1{left:0}.panel--2{left:267px;width:266px}.panel--3{left:533px}
.photo{position:absolute}
.brand-name{font-family:"Roboto",Arial,sans-serif;font-weight:500;color:var(--navy);text-align:center;letter-spacing:.3px}

/* outside: quote panel */
.quote-mark{position:absolute;left:0;width:267px;text-align:center;font-weight:700;font-size:58px;line-height:1;color:#9a9a9a}
.quote-mark--open{top:30px}.quote-mark--close{top:192px}
.quote{position:absolute;top:80px;left:10px;width:247px;text-align:center;font-weight:300;font-size:17px;line-height:1.45;color:#222}
.quote b{font-weight:400;font-size:21px}
.quote-photo{left:0;top:247px;width:267px;height:333px;background:linear-gradient(160deg,#e6e6e4 0%,#c9c9c7 45%,#7d7f86 100%)}

/* outside: contact panel */
.contact-brand{position:absolute;top:40px;left:0;width:266px;font-size:24px}
.contact-box{position:absolute;top:97px;left:0;width:266px;height:344px;background:var(--red);color:#fff;text-align:center;padding-top:40px}
.contact-tab{position:absolute;top:82px;left:71px;width:124px;height:28px;background:var(--yellow);border-radius:4px;font-weight:700;font-size:13px;line-height:28px;text-align:center;color:#333;box-shadow:0 2px 3px rgba(0,0,0,.2)}
.region{font-weight:700;font-size:11px;margin-bottom:5px}
.office{font-size:11px;line-height:17px}
.region-group{margin-bottom:22px}
.contact-foot{position:absolute;top:450px;left:0;width:266px;text-align:center;font-size:12px;color:#222}
.contact-phone{font-weight:700;font-size:15px;margin:2px 0 8px}
.contact-address{line-height:14px;margin:2px 0 8px}
.contact-web{font-size:12px;margin-top:2px}
.icon{display:block;margin:0 auto}

/* outside: cover panel */
.cover-brand{position:absolute;top:40px;left:0;width:267px;font-size:26px}
.cover-rule{position:absolute;top:92px;left:0;width:148px;height:3px;background:var(--red)}
.cover-photo{left:0;top:101px;width:267px;height:409px;background:linear-gradient(150deg,#d9dde2 0%,#9aa3ad 40%,#3e4e63 100%)}
.cover-stripe{position:absolute;top:436px;left:0;width:267px;height:10px;background:var(--green)}
.cover-title{position:absolute;top:383px;left:17px;width:221px;height:124px;background:var(--green);color:#fff;text-align:center;border:2px solid rgba(255,255,255,.35);padding-top:14px}
.cover-title span{display:block;font-weight:400;font-size:19px;letter-spacing:1px}
.cover-title strong{display:block;font-weight:500;font-size:46px;line-height:48px}
.cover-web{position:absolute;top:540px;left:0;width:267px;text-align:center;font-size:13px;color:#222}

/* inside */
.heading{font-weight:700;font-size:11px;color:var(--red);letter-spacing:.2px}
.heading em{font-style:normal;color:var(--green)}
.body-copy{font-family:"Roboto Condensed",Arial,sans-serif;font-size:6.8px;line-height:9.4px;color:var(--muted);text-align:justify}
.body-copy p{margin-bottom:6px}
.about{position:absolute;top:38px;left:24px;width:222px}
.about .block{margin-bottom:20px}
.about .heading{margin-bottom:7px}
.definition{font-size:7.5px;line-height:11px;color:#555}
.mission{font-size:7.5px;line-height:10px;color:#555}
.divider{width:78px;height:1px;background:#999;margin:10px 0 24px}

.panel--2{background:linear-gradient(180deg,#fff 40%,#f1f1f1 100%)}
.options-photo{left:0;top:0;width:266px;height:179px;background:linear-gradient(135deg,#5b6470 0%,#8c8f92 45%,#c9c4bb 100%)}
.options-rule{position:absolute;top:179px;left:28px;width:110px;height:3px;background:var(--green)}
.options{position:absolute;top:207px;left:20px;width:228px}
.option{position:relative;padding-left:24px;margin:12px 0 28px}
.option-icon{position:absolute;left:0;top:-2px}
.option h3{font-weight:500;font-size:9.5px;color:var(--navy);margin-bottom:7px}
.options-brand{position:absolute;top:526px;left:0;width:266px;font-size:16px}

.onsite{position:absolute;top:38px;left:20px;width:228px}
.onsite .heading{margin-bottom:7px}
.sector{position:relative;padding-left:24px;margin-top:24px}
.sector h3{font-weight:500;font-size:9.5px;color:var(--navy);margin-bottom:5px}
.sector .option-icon{top:-2px}
.tick-cols{display:flex;gap:16px}
.tick-list{list-style:none;font-size:7px;line-height:10.5px;color:#555;width:96px}
.tick-list li{padding-left:9px;text-indent:-9px}
.tick-list li::before{content:"\2713";color:var(--red);font-size:6px;margin-right:4px}
.onsite-photo{left:0;top:442px;width:267px;height:138px;background:linear-gradient(120deg,#f3f3f3 0%,#d7dade 50%,#9fa9b5 100%)}
</style>
</head>
<body>

<section class="sheet sheet--outside" aria-label="Brochure outside">
  <div class="panel panel--1">
    <div class="quote-mark quote-mark--open">&ldquo;</div>
    <p class="quote"><b>YES</b> the <b>CANDIDATE</b><br>meets the requirements,<br><b>YEAH</b> they <b>HAVE</b> the<br>skills, but do they <b>TARN?</b></p>
    <div class="quote-mark quote-mark--close">&rdquo;</div>
    <div class="photo quote-photo" role="img" aria-label="Photo of a smiling young professional woman in glasses holding a tablet in a bright office"></div>
  </div>

  <div class="panel panel--2">
    <div class="brand-name contact-brand">Tarn Workforce</div>
    <div class="contact-box">
      <div class="region-group">
        <div class="region">Georgia</div>
        <div class="office">Alder Falls – 555-010-4821</div>
        <div class="office">Kestrel Hill – 555-010-3377</div>
        <div class="office">Saltmarsh Bay – 555-010-6912</div>
        <div class="office">Linden Cross – 555-010-2284</div>
      </div>
      <div class="region-group">
        <div class="region">Indiana</div>
        <div class="office">Fernvale – 555-010-7745</div>
      </div>
      <div class="region-group">
        <div class="region">Pennsylvania</div>
        <div class="office">Ridgeport – 555-010-5530</div>
        <div class="office">Larkmoor – 555-010-8816</div>
      </div>
      <div class="region-group">
        <div class="region">Texas</div>
        <div class="office">Cedar Flats – 555-010-9063</div>
      </div>
    </div>
    <div class="contact-tab">CONTACT US</div>
    <div class="contact-foot">
      <svg class="icon" width="10" height="10" viewBox="0 0 24 24" aria-hidden="true"><path fill="#3a3d8c" d="M6.6 10.8a15.1 15.1 0 0 0 6.6 6.6l2.2-2.2a1 1 0 0 1 1-.25 11.4 11.4 0 0 0 3.6.57 1 1 0 0 1 1 1V20a1 1 0 0 1-1 1A17 17 0 0 1 3 4a1 1 0 0 1 1-1h3.5a1 1 0 0 1 1 1c0 1.25.2 2.45.57 3.6a1 1 0 0 1-.25 1z"/></svg>
      <div class="contact-phone">555-010-4821</div>
      <svg class="icon" width="9" height="11" viewBox="0 0 24 30" aria-hidden="true"><path fill="#3a3d8c" d="M12 0a10 10 0 0 0-10 10c0 7.5 10 20 10 20s10-12.5 10-20A10 10 0 0 0 12 0zm0 14a4 4 0 1 1 0-8 4 4 0 0 1 0 8z"/></svg>
      <div class="contact-address">480 Alder Row, Suite 12,<br>Alder Falls, GA 30000</div>
      <svg class="icon" width="8" height="8" viewBox="0 0 10 10" aria-hidden="true"><circle cx="5" cy="5" r="4.5" fill="#3a3d8c"/></svg>
      <div class="contact-web">www.TarnWorkforce-example.com</div>
    </div>
  </div>

  <div class="panel panel--3">
    <div class="brand-name cover-brand">Tarn Workforce</div>
    <div class="cover-rule"></div>
    <div class="photo cover-photo" role="img" aria-label="Photo of two young colleagues working together at a laptop"></div>
    <div class="cover-stripe"></div>
    <div class="cover-title"><span>ATTAINING</span><strong>CLIENT</strong><span>OBJECTIVES</span></div>
    <div class="cover-web">www.TarnWorkforce-example.com</div>
  </div>
</section>

<section class="sheet sheet--inside" aria-label="Brochure inside">
  <div class="panel panel--1">
    <div class="about">
      <div class="block">
        <h2 class="heading">DEFINITION OF TARN – <em>VERB</em></h2>
        <p class="definition">To be in harmony or accord; To Fit; Agree<br>"Yes the candidate meets the requirements, yeah they have the skills, but do they Tarn?"</p>
      </div>
      <div class="block">
        <h2 class="heading">MISSION</h2>
        <p class="mission">At Tarn Workforce, we are passionate in our pursuit to change lives by connecting great people with great organizations.</p>
      </div>
      <div class="divider"></div>
      <div class="block">
        <h2 class="heading">WHO <em>WE ARE</em></h2>
        <div class="body-copy"><p>At Tarn Workforce, we are invested in helping people and improving lives. We partner with great organizations who want to grow, and with driven individuals eager to build better careers. Every placement should make a positive impact.</p></div>
      </div>
      <div class="block">
        <h2 class="heading">WHAT <em>WE DO</em></h2>
        <div class="body-copy">
          <p>At Tarn Workforce we do things a little differently. We don't act as a pipeline, simply pumping workers into your organization. We provide professional development and training so every candidate arrives with the skills and attitude they need to succeed.</p>
          <p>We believe in providing our partners with not only the most prepared talent, but also the most secure. Every candidate passes a thorough battery of tests and checks, including background and drug screening, before placement.</p>
          <p>Tarn Workforce is powered by a recruiting engine that never stops. Our Temporary, Temp to Hire and Direct Hire services meet the needs of growing companies while delivering a better experience.</p>
          <p>At Tarn Workforce, we have a golden opportunity to positively impact the lives of employees and job seekers. We consider it a privilege and we love what we do.</p>
          <p>We look forward to learning about your specific needs and exploring how Tarn Workforce can bring immediate and lasting value.</p>
        </div>
      </div>
    </div>
  </div>

  <div class="panel panel--2">
    <div class="photo options-photo" role="img" aria-label="Photo of two businessmen meeting over a laptop in a modern office"></div>
    <div class="options-rule"></div>
    <div class="options">
      <h2 class="heading">STAFFING <em>OPTIONS</em></h2>
      <div class="option">
        <svg class="option-icon" width="15" height="15" viewBox="0 0 20 20" aria-hidden="true"><circle cx="10" cy="10" r="10" fill="#3a3d8c"/><circle cx="10" cy="10" r="5" fill="none" stroke="#f5c51b" stroke-width="1.8"/><path d="M10 7.5V10l1.8 1.2" stroke="#f5c51b" stroke-width="1.4" fill="none"/></svg>
        <h3>Temporary</h3>
        <div class="body-copy"><p>This is an ideal solution that gives flexibility to companies with projects, seasonal spikes or gaps when vacancies occur. It lets you ramp up without adding new associates to your payroll.</p></div>
      </div>
      <div class="option">
        <svg class="option-icon" width="15" height="15" viewBox="0 0 20 20" aria-hidden="true"><circle cx="10" cy="10" r="10" fill="#3a3d8c"/><circle cx="9" cy="9" r="3.6" fill="none" stroke="#f5c51b" stroke-width="1.6"/><path d="M11.6 11.6l3 3" stroke="#f5c51b" stroke-width="1.8"/></svg>
        <h3>Temp to Hire</h3>
        <div class="body-copy"><p>Is a way for clients to test the waters and see if the candidate will prove themselves a good long term fit. You review performance and attitude for a set period while the associate stays on our payroll.</p></div>
      </div>
      <div class="option">
        <svg class="option-icon" width="15" height="15" viewBox="0 0 20 20" aria-hidden="true"><circle cx="10" cy="10" r="10" fill="#3a3d8c"/><rect x="5.5" y="7" width="9" height="7" rx="1" fill="none" stroke="#f5c51b" stroke-width="1.5"/><path d="M8 7V5.5h4V7" stroke="#f5c51b" stroke-width="1.4" fill="none"/></svg>
        <h3>Direct Hire</h3>
        <div class="body-copy"><p>When a client has a long-term or highly skilled need, direct hire is an ideal program. We recruit and screen candidates to be interviewed with the client, and the chosen candidate goes directly on the client's payroll from day one.</p></div>
      </div>
    </div>
    <div class="brand-name options-brand">Tarn Workforce</div>
  </div>

  <div class="panel panel--3">
    <div class="onsite">
      <h2 class="heading">ONSITE <em>MANAGEMENT</em></h2>
      <div class="body-copy"><p>Tarn Workforce offers Onsite Management for clients that utilize a high volume of Tarn associates. Our Onsite Manager will in essence serve as an extension of our client's management team. They are on the production floor 75% of the time, not in an office. Tarn Workforce's Onsite Manager is charged with training Tarn Associate's, coaching, counseling, driving production as well as quality and overall safety.</p></div>

      <div class="sector">
        <svg class="option-icon" width="15" height="15" viewBox="0 0 20 20" aria-hidden="true"><circle cx="10" cy="10" r="10" fill="#3a3d8c"/><path d="M5 14V9l3 2V9l3 2V7h4v7z" fill="#f5c51b"/></svg>
        <h3>Light Industrial</h3>
        <div class="tick-cols">
          <ul class="tick-list"><li>Manufacturing</li><li>Logistics</li><li>Packaging</li><li>Assembly</li></ul>
          <ul class="tick-list"><li>Printing</li><li>Fulfillment</li><li>Hospitality</li></ul>
        </div>
      </div>
      <div class="sector">
        <svg class="option-icon" width="15" height="15" viewBox="0 0 20 20" aria-hidden="true"><circle cx="10" cy="10" r="10" fill="#3a3d8c"/><circle cx="10" cy="8" r="2.6" fill="#f5c51b"/><path d="M5.5 15a4.5 4.5 0 0 1 9 0z" fill="#f5c51b"/></svg>
        <h3>Professional</h3>
        <div class="tick-cols">
          <ul class="tick-list"><li>Accounting</li><li>Administrative</li><li>Call Center</li><li>Customer Service</li></ul>
          <ul class="tick-list"><li>Data Entry</li><li>Executive<br>Management</li><li>Legal</li><li>Sales</li></ul>
        </div>
      </div>
      <div class="sector">
        <svg class="option-icon" width="15" height="15" viewBox="0 0 20 20" aria-hidden="true"><circle cx="10" cy="10" r="10" fill="#3a3d8c"/><path d="M6 14l5-5m-1-3.5a3 3 0 0 0 4 4" stroke="#f5c51b" stroke-width="1.8" fill="none"/></svg>
        <h3>Skilled Trades</h3>
        <div class="tick-cols">
          <ul class="tick-list"><li>Electrical</li><li>Maintenance</li><li>Welding</li><li>Painting</li></ul>
          <ul class="tick-list"><li>C&amp;C Operators/<br>Programmers</li><li>Machine<br>Operators</li><li>Plumbing</li></ul>
        </div>
      </div>
    </div>
    <div class="photo onsite-photo" role="img" aria-label="Photo of a diverse team of colleagues talking in a bright open-plan office"></div>
  </div>
</section>

</body>
</html>
```